We need a web page design for a new company called "Brambel". We provide an innovative music sharing mobile application that allows music listeners to share their music without paying for a monthly subscription. We would like to incorporate the attached logo and color scheme. The final design should communicate music gifting and sharing.

Industry/Entity Type

It Company

```html
<!DOCTYPE html>
<html lang="en">
<head>
<meta charset="utf-8">
<title>Brambel – Music Sharing</title>
<link rel="stylesheet" href="https://fonts.googleapis.com/css2?family=Roboto:ital,wght@0,400;0,500;0,700;1,700&family=Lato:wght@400;700&display=swap">
<style>
:root{
  --green:#64a70b;
  --green-light:#8cc342;
  --orange:#f6921e;
  --orange-frame:#f7941d;
  --ink:#333333;
  --grey-btn:#9a9a9a;
  --cta-bg:#ece7d8;
  --cta-border:#d8d2bf;
  --footer:#333333;
  --footer-base:#262626;
  --white:#ffffff;
}
*{margin:0;padding:0;box-sizing:border-box}
html,body{width:821px;height:1200px;overflow:hidden;background:var(--white)}
body{position:relative;font-family:"Roboto",Arial,sans-serif;color:var(--ink)}

/* header */
.site-header{position:absolute;left:0;top:0;width:821px;height:60px;background:var(--green)}
.brand{position:absolute;left:120px;top:15px;display:flex;align-items:center;gap:7px;color:var(--white)}
.brand-dot{width:30px;height:30px;border-radius:50%;background:var(--white)}
.brand-name{font-size:29px;font-weight:500;line-height:30px;color:var(--white)}
.main-nav{position:absolute;left:379px;top:0;height:60px;display:flex}
.main-nav a{display:block;height:60px;line-height:78px;padding:0 12px;font-size:9px;font-weight:700;color:var(--white);text-decoration:none}
.main-nav a.active{background:var(--white);color:var(--ink);padding:0 10px;margin-right:2px}
.account{position:absolute;left:680px;top:13px;font-size:8px;color:var(--white);letter-spacing:.3px}

/* hero */
.hero{position:absolute;left:0;top:60px;width:821px;height:263px;background:linear-gradient(90deg,#e9ddd6 0%,#f4ece8 35%,#ffffff 55%,#fbe9f6 75%,#f3c8ea 100%)}
.hero-photo{position:absolute;left:60px;top:0;width:400px;height:263px;background:radial-gradient(ellipse at 50% 45%,#e8c2ad 0%,#d9a98f 35%,#b9a8a0 60%,rgba(240,234,230,0) 80%)}
.hero-smoke{position:absolute;left:500px;top:0;width:321px;height:263px;background:radial-gradient(ellipse at 70% 40%,rgba(216,92,190,.45) 0%,rgba(240,170,225,.25) 40%,rgba(255,255,255,0) 70%)}
.hero-card{position:absolute;left:566px;top:66px;width:174px;height:100px;background:rgba(255,255,255,.55);text-align:center}
.hero-dot{width:34px;height:34px;border-radius:50%;background:var(--green);margin:-18px auto 0}
.hero-name{font-size:20px;font-weight:500;color:var(--ink);margin-top:10px;line-height:22px}
.hero-btns{position:absolute;left:41px;top:67px;display:flex;height:18px}
.hero-btns span{display:block;height:18px;line-height:18px;font-size:8px;color:var(--white);background:var(--green)}
.hero-btns .arrow{width:18px}
.hero-btns .label{width:56px;background:#4a4a4a}

/* features */
.features{position:absolute;left:113px;top:323px;width:640px;height:130px;display:flex}
.feature{position:relative;width:160px;height:130px;text-align:center;color:var(--white)}
.feature:nth-child(odd){background:var(--green)}
.feature:nth-child(even){background:var(--green-light)}
.feature-icon{position:absolute;left:38px;top:-43px;width:84px;height:84px;border-radius:50%;background:var(--white);border:3px solid var(--green);display:flex;align-items:center;justify-content:center}
.feature-title{position:absolute;left:0;right:0;top:51px;font-size:12.5px;font-weight:500}
.feature-text{position:absolute;left:14px;right:14px;top:70px;font-size:9.5px;line-height:11.5px}
.feature-more{position:absolute;left:69px;bottom:0;width:22px;height:20px;background:var(--orange);border:2px solid var(--white);border-bottom:none;color:var(--white);font-size:16px;font-weight:700;line-height:18px}

/* section headings */
.section-title{position:absolute;left:113px;height:16px;border-left:2px solid var(--green);padding-left:5px;font-size:14px;line-height:16px;font-weight:400;color:var(--ink)}
.pager{position:absolute;display:flex;gap:2px}
.pager span{width:16px;height:15px;display:block;color:var(--white);font-size:10px;line-height:15px;text-align:center}

/* trending */
.track{position:absolute;top:509px;width:149px}
.track-art{width:149px;height:148px;border:5px solid var(--green)}
.track-art.hot{border-color:var(--orange-frame)}
.track-title{font-size:9px;font-weight:700;font-style:italic;margin-top:5px;color:var(--ink)}
.track-actions{display:flex;justify-content:space-between;margin-top:6px;padding:0 2px 7px;border-bottom:2px solid var(--green)}
.btn-share,.btn-gift{display:block;width:40px;height:15px;line-height:15px;text-align:center;font-size:8px;color:var(--white)}
.btn-share{background:var(--green)}
.btn-gift{background:var(--grey-btn)}

/* cta */
.cta{position:absolute;left:113px;top:726px;width:640px;height:59px;background:var(--cta-bg);border:1px solid var(--cta-border)}
.cta-text{position:absolute;left:6px;top:20px;font-size:14px;color:var(--ink)}
.cta-btn{position:absolute;left:543px;top:14px;width:87px;height:28px;line-height:28px;text-align:center;background:var(--green);color:var(--white);font-size:10px;font-weight:500}

/* categories */
.read-more{position:absolute;left:684px;top:815px;width:67px;height:20px;line-height:20px;text-align:center;background:var(--orange);color:var(--ink);font-size:8px;font-weight:500}
.cat-rule{position:absolute;left:113px;top:845px;width:640px;height:1px;background:#eeeeee}
.cat-col{position:absolute;top:856px;width:80px;list-style:none}
.cat-item{position:relative;height:26.6px;border-bottom:1px solid #ececec;font-size:9px;line-height:18px;padding-left:16px;color:#444}
.cat-item::before{content:"";position:absolute;left:1px;top:4px;width:10px;height:10px;border-radius:50%;background:#c9c9c9}
.cat-item::after{content:"›";position:absolute;right:0;top:5px;width:8px;height:8px;background:var(--green);color:var(--white);font-size:8px;line-height:7px;text-align:center}
.cat-item.current{color:var(--green)}

/* footer */
.site-footer{position:absolute;left:0;top:1038px;width:821px;height:134px;background:var(--footer);border-top:3px solid var(--green);font-family:"Lato",Arial,sans-serif;color:var(--white)}
.footer-title{position:absolute;top:10px;font-size:13px;font-weight:400;color:var(--white);padding-bottom:4px;border-bottom:1px solid #4a4a4a}
.footer-sep{position:absolute;top:14px;width:1px;height:108px;background:#444}
.quick-links{position:absolute;left:113px;top:36px;list-style:none;font-size:9px;line-height:14.4px}
.quick-links li::before{content:"›";margin-right:6px}
.news-item{position:absolute;left:229px;display:flex;gap:9px}
.news-date{width:25px;text-align:center}
.news-day{height:14px;line-height:14px;background:var(--green);font-size:9px;font-weight:700}
.news-month{height:10px;line-height:10px;background:#eeeeee;color:var(--ink);font-size:7px;font-weight:700}
.news-text{font-size:8.5px;line-height:10px;width:122px}
.news-text b{display:block}
.newsletter-text{position:absolute;left:430px;top:37px;width:140px;font-size:8px;line-height:12.5px}
.newsletter-input{position:absolute;left:430px;top:70px;width:142px;height:18px;background:var(--white);color:#888;font-size:7px;font-style:italic;line-height:18px;padding-left:4px}
.newsletter-btn{position:absolute;left:430px;top:96px;width:72px;height:19px;line-height:19px;text-align:center;background:var(--green);font-size:10px;font-weight:700;letter-spacing:.3px}
.footer-brand{position:absolute;left:622px;top:44px;display:flex;align-items:center;gap:6px}
.footer-brand .brand-dot{width:22px;height:22px}
.footer-brand .brand-name{font-size:24px;font-weight:400;font-family:"Lato",Arial,sans-serif}
.social{position:absolute;left:642px;top:95px;display:flex;gap:7px}
.social span{width:16px;height:16px;border-radius:50%;background:#555}
.social span.on{background:var(--green)}
.footer-base{position:absolute;left:0;top:1172px;width:821px;height:28px;background:var(--footer-base);color:#dddddd;font-family:"Lato",Arial,sans-serif;font-size:8px;line-height:28px;text-align:center}
.footer-base b{color:var(--white)}
</style>
</head>
<body>

<header class="site-header">
  <div class="brand"><span class="brand-dot"></span><span class="brand-name">Brambel</span></div>
  <nav class="main-nav">
    <a class="active" href="#">HOME</a>
    <a href="#">SERVICES</a>
    <a href="#">TIMETABLE</a>
    <a href="#">NEWS</a>
    <a href="#">FEATURES</a>
    <a href="#">CONTACTS</a>
  </nav>
  <div class="account">LOGIN &nbsp;|&nbsp; SIGNUP</div>
</header>

<section class="hero">
  <div class="hero-photo" role="img" aria-label="Photo of a woman listening to music on large headphones with eyes closed"></div>
  <div class="hero-smoke" role="img" aria-label="Soft pink smoke swirls over a white background"></div>
  <div class="hero-card">
    <div class="hero-dot"></div>
    <div class="hero-name">Brambel</div>
    <div class="hero-btns"><span class="arrow">&lt;</span><span class="label">READ MORE</span><span class="arrow">&gt;</span></div>
  </div>
</section>

<section class="features">
  <div class="feature">
    <div class="feature-icon">
      <svg width="36" height="36" viewBox="0 0 36 36"><path d="M13 6 L30 3 V24 a5 5 0 1 1 -3 -4.6 V10 L16 12 V28 a5 5 0 1 1 -3 -4.6 Z" fill="var(--orange)"/></svg>
    </div>
    <div class="feature-title">UPLOAD MUSIC &amp; AUDIO</div>
    <div class="feature-text">Lorem Ipsum is simply dummy text of the printing.</div>
    <div class="feature-more">+</div>
  </div>
  <div class="feature">
    <div class="feature-icon">
      <svg width="40" height="40" viewBox="0 0 40 40"><path d="M6 24 V20 a14 14 0 0 1 28 0 V24" fill="none" stroke="var(--orange)" stroke-width="4"/><rect x="4" y="21" width="9" height="15" rx="3" fill="var(--orange)"/><rect x="27" y="21" width="9" height="15" rx="3" fill="var(--orange)"/></svg>
    </div>
    <div class="feature-title">LISTEN &amp; DISCOVER</div>
    <div class="feature-text">Lorem Ipsum is simply dummy text of the printing fdsjoid.</div>
    <div class="feature-more">+</div>
  </div>
  <div class="feature">
    <div class="feature-icon">
      <svg width="40" height="40" viewBox="0 0 40 40"><circle cx="15" cy="11" r="7" fill="var(--orange)"/><path d="M2 34 a13 12 0 0 1 26 0 Z" fill="var(--orange)"/><circle cx="29" cy="19" r="5" fill="var(--orange)"/><path d="M20 36 a9 9 0 0 1 18 0 Z" fill="var(--orange)"/></svg>
    </div>
    <div class="feature-title">CONNECT</div>
    <div class="feature-text">Lorem Ipsum is simply dummy text of the printing.</div>
    <div class="feature-more">+</div>
  </div>
  <div class="feature">
    <div class="feature-icon">
      <svg width="40" height="40" viewBox="0 0 40 40"><g stroke="var(--orange)" stroke-width="3"><line x1="20" y1="20" x2="8" y2="8"/><line x1="20" y1="20" x2="33" y2="9"/><line x1="20" y1="20" x2="10" y2="32"/><line x1="20" y1="20" x2="32" y2="31"/></g><g fill="var(--orange)"><circle cx="20" cy="20" r="7"/><circle cx="8" cy="8" r="5"/><circle cx="33" cy="9" r="4"/><circle cx="10" cy="32" r="4"/><circle cx="32" cy="31" r="5"/></g></svg>
    </div>
    <div class="feature-title">SHARE</div>
    <div class="feature-text">Lorem Ipsum is simply dummy text of the printing fdsjoid.</div>
    <div class="feature-more">+</div>
  </div>
</section>

<h2 class="section-title" style="top:483px">TRENDING MUSIC &amp; AUDIO</h2>
<div class="pager" style="left:718px;top:483px"><span style="background:#cccccc">‹</span><span style="background:var(--green)">›</span></div>

<article class="track" style="left:113px">
  <div class="track-art" role="img" aria-label="Album cover: black and white portrait of a pop singer" style="background:linear-gradient(135deg,#3a3a3a,#bdbdbd 60%,#2a2a2a)"></div>
  <div class="track-title">Lorem ipsum dolor sfgjit rem Ipsumis</div>
  <div class="track-actions"><span class="btn-share">SHARE</span><span class="btn-gift">GIFT</span></div>
</article>
<article class="track" style="left:276px">
  <div class="track-art hot" role="img" aria-label="Album cover: ornate copper lettering on black, with a play button" style="background:radial-gradient(circle at 50% 50%,#8a4a2a 0%,#5a2a18 35%,#111 70%)">
    <svg width="139" height="138" viewBox="0 0 139 138"><circle cx="70" cy="69" r="17" fill="rgba(80,80,80,.6)"/><path d="M64 60 L79 69 L64 78 Z" fill="#ddd"/></svg>
  </div>
  <div class="track-title">Lorem ipsum dolor sfgjit rem Ipsumis</div>
  <div class="track-actions"><span class="btn-share">SHARE</span><span class="btn-gift">GIFT</span></div>
</article>
<article class="track" style="left:439px">
  <div class="track-art" role="img" aria-label="Album cover: bold magenta and white greatest hits graphic" style="background:linear-gradient(90deg,#e0197d 0%,#f5f5f5 30%,#e0197d 55%,#f5f5f5 75%,#e0197d 100%)"></div>
  <div class="track-title">Lorem ipsum dolor sfgjit rem Ipsumis</div>
  <div class="track-actions"><span class="btn-share">SHARE</span><span class="btn-gift">GIFT</span></div>
</article>
<article class="track" style="left:603px">
  <div class="track-art" role="img" aria-label="Album cover: dark gothic metal artwork in gold and brown tones" style="background:radial-gradient(circle at 50% 40%,#b08a3a 0%,#6b4a1e 45%,#241608 100%)"></div>
  <div class="track-title">Lorem ipsum dolor sfgjit rem Ipsumis</div>
  <div class="track-actions"><span class="btn-share">SHARE</span><span class="btn-gift">GIFT</span></div>
</article>

<section class="cta">
  <p class="cta-text">So are you ready to discover new music and sounds and share them with the world?</p>
  <span class="cta-btn">SIGN UP NOW</span>
</section>

<h2 class="section-title" style="top:817px">MUSIC CATEGORIES</h2>
<span class="read-more">READ MORE</span>
<div class="cat-rule"></div>

<ul class="cat-col" style="left:113px">
  <li class="cat-item current">Acoustic</li><li class="cat-item">Music-Pack</li><li class="cat-item">Drum'n' Bass</li><li class="cat-item">Alternative</li><li class="cat-item">Eurodance</li><li class="cat-item">Ambient</li>
</ul>
<ul class="cat-col" style="left:220px">
  <li class="cat-item">Acoustic</li><li class="cat-item">Music-Pack</li><li class="cat-item">Drum'n' Bass</li><li class="cat-item">Alternative</li><li class="cat-item">Eurodance</li><li class="cat-item">Ambient</li>
</ul>
<ul class="cat-col" style="left:330px">
  <li class="cat-item">Acoustic</li><li class="cat-item">Music-Pack</li><li class="cat-item">Drum'n' Bass</li><li class="cat-item">Alternative</li><li class="cat-item">Eurodance</li><li class="cat-item">Ambient</li>
</ul>
<ul class="cat-col" style="left:440px">
  <li class="cat-item">Acoustic</li><li class="cat-item">Music-Pack</li><li class="cat-item">Drum'n' Bass</li><li class="cat-item">Alternative</li><li class="cat-item">Eurodance</li><li class="cat-item">Ambient</li>
</ul>
<ul class="cat-col" style="left:553px">
  <li class="cat-item">Acoustic</li><li class="cat-item">Music-Pack</li><li class="cat-item">Drum'n' Bass</li><li class="cat-item">Alternative</li><li class="cat-item">Eurodance</li><li class="cat-item">Ambient</li>
</ul>
<ul class="cat-col" style="left:668px;width:84px">
  <li class="cat-item">Acoustic</li><li class="cat-item">Music-Pack</li><li class="cat-item">Drum'n' Bass</li><li class="cat-item">Alternative</li><li class="cat-item">Eurodance</li><li class="cat-item">Ambient</li>
</ul>

<footer class="site-footer">
  <h3 class="footer-title" style="left:113px;width:85px">Quick Links</h3>
  <ul class="quick-links">
    <li>Home</li><li>Services</li><li>Timetable</li><li>News</li><li>Features</li><li>Contact Us</li>
  </ul>
  <div class="footer-sep" style="left:210px"></div>

  <h3 class="footer-title" style="left:229px;width:157px">News Updates</h3>
  <div class="pager" style="left:362px;top:14px"><span style="background:var(--green);width:11px;height:11px;line-height:11px">‹</span><span style="background:var(--green);width:11px;height:11px;line-height:11px">›</span></div>
  <div class="news-item" style="top:42px">
    <div class="news-date"><div class="news-day">12</div><div class="news-month">NOV</div></div>
    <div class="news-text"><b>Vero eros accumsaet odio</b>quis nostrud exetiperj suscipit nisl ut aliquip ex ea commod</div>
  </div>
  <div class="news-item" style="top:89px">
    <div class="news-date"><div class="news-day">20</div><div class="news-month">NOV</div></div>
    <div class="news-text"><b>Vero eros accumsaet odio</b>quis nostrud exetiperj suscipit nisl ut aliquip ex ea commod</div>
  </div>
  <div class="footer-sep" style="left:408px"></div>

  <h3 class="footer-title" style="left:430px;width:140px">Newsletter Sign Up</h3>
  <p class="newsletter-text">Lorem ipsudolor sit coec adipiscing elitsite amet</p>
  <div class="newsletter-input">Email Address</div>
  <span class="newsletter-btn">SUBSCRIBE</span>
  <div class="footer-sep" style="left:605px"></div>

  <div class="footer-brand"><span class="brand-dot"></span><span class="brand-name">Brambel</span></div>
  <div class="social"><span></span><span class="on"></span><span></span><span></span></div>
</footer>
<div class="footer-base">© 2014 <b>BrambelMusic</b>. All Rights Reserved.</div>

</body>
</html>
```